Business Card Design

We are looking for a business card designed for our landscaping company. We do landscaping installation & Maintenance Services. We would like to see designs that have basic landscaping in background. We also think it is important to have both of our names and phone numbers on the card. We need something that stands out a little whether it is shape of the card or thickness or design.

Business

Bramblewood Yardworks, bramblewoodyard@mailvista.net, Owen Platt 555-273-9104, Daniel Korbin 555-618-3927

```html
<!DOCTYPE html>
<html lang="en">
<head>
<meta charset="utf-8">
<title>Bramblewood Yardworks – Business Card</title>
<link href="https://fonts.googleapis.com/css2?family=Noto+Sans:wght@400&display=swap" rel="stylesheet">
<style>
  :root {
    --backdrop: #e9e6e1;
    --card-white: #ffffff;
    --card-shade: #ededed;
    --swoosh-grey: #cfcfcf;
    --band-blue: #1a73c9;
    --band-blue-deep: #0f5fb0;
    --ink: #1c1c1c;
    --rule: #111111;
    --on-blue: #ffffff;
  }
  html, body {
    margin: 0;
    width: 1200px;
    height: 892px;
    overflow: hidden;
    background: var(--backdrop);
    font-family: "Noto Sans", sans-serif;
  }
  .canvas {
    position: relative;
    width: 1200px;
    height: 892px;
  }
  .business-card {
    position: absolute;
    left: 220px;
    top: 229px;
    width: 760px;
    height: 434px;
    background: linear-gradient(135deg, var(--card-white) 40%, var(--card-shade) 100%);
    box-shadow: 0 14px 30px rgba(0,0,0,0.22);
    overflow: hidden;
  }
  .card-band {
    position: absolute;
    inset: 0;
  }
  .company-name {
    position: absolute;
    left: 52px;
    top: 40px;
    margin: 0;
    font-size: 30px;
    font-weight: 400;
    letter-spacing: 0.5px;
    color: var(--ink);
  }
  .divider {
    position: absolute;
    left: 458px;
    top: 44px;
    width: 2px;
    height: 236px;
    background: var(--rule);
  }
  .contacts {
    position: absolute;
    left: 482px;
    top: 52px;
    color: var(--ink);
  }
  .contact { margin-bottom: 30px; }
  .contact-name {
    font-size: 24px;
    line-height: 30px;
    letter-spacing: 0.5px;
  }
  .contact-phone {
    display: flex;
    align-items: center;
    gap: 10px;
    font-size: 28px;
    line-height: 36px;
    letter-spacing: 1px;
  }
  .phone-icon { width: 20px; height: 20px; flex: none; }
  .email {
    position: absolute;
    right: 40px;
    bottom: 42px;
    font-size: 22px;
    letter-spacing: 0.5px;
    color: var(--on-blue);
  }
</style>
</head>
<body>
<main class="canvas">
  <section class="business-card">
    <svg class="card-band" width="760" height="434" viewBox="0 0 760 434" aria-hidden="true">
      <defs>
        <linearGradient id="bandFill" x1="0" y1="0" x2="1" y2="1">
          <stop offset="0" stop-color="var(--band-blue)"/>
          <stop offset="1" stop-color="var(--band-blue-deep)"/>
        </linearGradient>
      </defs>
      <path d="M0 330 C 220 330, 360 320, 440 296 C 520 272, 600 262, 760 262 L 760 434 L 0 434 Z" fill="var(--swoosh-grey)"/>
      <path d="M0 350 C 230 350, 370 338, 450 312 C 530 288, 610 280, 760 280 L 760 434 L 0 434 Z" fill="url(#bandFill)"/>
    </svg>

    <h1 class="company-name">Bramblewood Yardworks</h1>
    <div class="divider"></div>

    <div class="contacts">
      <div class="contact">
        <div class="contact-name">Owen Platt</div>
        <div class="contact-phone">
          <svg class="phone-icon" viewBox="0 0 20 20" aria-hidden="true">
            <rect width="20" height="20" fill="var(--ink)"/>
            <path d="M5 5 l3 0 l1 3 l-2 1 a7 7 0 0 0 4 4 l1 -2 l3 1 l0 3 a10 10 0 0 1 -10 -10 z" fill="#fff"/>
          </svg>
          <span>555-273-9104</span>
        </div>
      </div>
      <div class="contact">
        <div class="contact-name">Daniel Korbin</div>
        <div class="contact-phone">
          <svg class="phone-icon" viewBox="0 0 20 20" aria-hidden="true">
            <rect width="20" height="20" fill="var(--ink)"/>
            <path d="M5 5 l3 0 l1 3 l-2 1 a7 7 0 0 0 4 4 l1 -2 l3 1 l0 3 a10 10 0 0 1 -10 -10 z" fill="#fff"/>
          </svg>
          <span>555-618-3927</span>
        </div>
      </div>
    </div>

    <div class="email">bramblewoodyard@mailvista.net</div>
  </section>
</main>
</body>
</html>
```